Every Shelf Set Neatly or ESN Organized needs a business card design. ESN Organized is a professi

We need a business card design that is clean, sharp and conveys a sense of organization. I already have a logo.

Target Market(s)

Families (specifically mothers), small business owners, parents, seniors

Industry/Entity Type

Business

Contact Information for Business Card

My website is www.esnorganized-example.com and my Facebook page is http://www.sociallink-example.com/everyshelfsetneatly. The phone number is 418-552-7094 and I want to be listed as Lorna M. Pelham, Owner

Requirements
Must have
• My logo.

```html
<!DOCTYPE html>
<html lang="en">
<head>
<meta charset="utf-8">
<title>ESN Organized – Business Card</title>
<link rel="stylesheet" href="https://fonts.googleapis.com/css2?family=Montserrat:wght@400&family=Open+Sans:wght@400;600;700&display=swap">
<style>
  :root {
    --stage: #000000;
    --card-front: #f3f3f3;
    --brand-blue: #1a7fd6;
    --ink: #1c1c1c;
    --deep-blue: #0a5aa8;
    --bright-blue: #0b7fd8;
    --white: #ffffff;
  }
  html, body {
    margin: 0;
    width: 1200px;
    height: 900px;
    overflow: hidden;
    background: var(--stage);
  }
  .canvas {
    position: relative;
    width: 1200px;
    height: 900px;
  }
  .card {
    position: absolute;
    top: 200px;
    width: 310px;
    height: 502px;
    box-sizing: border-box;
  }
  .card--front {
    left: 265px;
    background: var(--card-front);
    border-radius: 60px 0 60px 0;
  }
  .card--back {
    left: 641px;
    width: 309px;
    border-radius: 0 60px 0 60px;
    overflow: hidden;
  }
  .back-texture {
    position: absolute;
    inset: 0;
    background:
      linear-gradient(160deg, rgba(255,255,255,0.06) 0%, rgba(0,0,0,0) 40%),
      linear-gradient(180deg, var(--bright-blue) 0%, #0c74cc 55%, var(--deep-blue) 100%);
  }
  .brand-name {
    position: absolute;
    top: 48px;
    left: 0;
    width: 100%;
    margin: 0;
    text-align: center;
    font-family: "Open Sans", sans-serif;
    font-weight: 600;
    font-size: 40px;
    line-height: 1;
    color: var(--brand-blue);
  }
  .tagline {
    position: absolute;
    left: 0;
    width: 100%;
    margin: 0;
    text-align: center;
    font-family: "Montserrat", sans-serif;
    font-weight: 400;
  }
  .tagline__top {
    display: block;
    font-size: 17px;
    letter-spacing: 2.2px;
    line-height: 1;
  }
  .tagline__main {
    display: block;
    font-size: 27px;
    letter-spacing: 6.5px;
    line-height: 1;
    margin-top: 8px;
  }
  .card--front .tagline { top: 111px; color: var(--ink); }
  .card--back .tagline { top: 385px; color: var(--white); }
  .card--back .tagline__top { font-size: 15px; letter-spacing: 2.4px; }
  .card--back .tagline__main { font-size: 24px; letter-spacing: 6px; margin-top: 6px; }

  .person {
    position: absolute;
    left: 30px;
    top: 310px;
    font-family: "Open Sans", sans-serif;
  }
  .person__name {
    margin: 0;
    font-weight: 700;
    font-size: 17px;
    color: var(--brand-blue);
    line-height: 1.2;
  }
  .person__role {
    margin: 1px 0 0;
    font-size: 13px;
    color: var(--ink);
  }
  .contact-list {
    position: absolute;
    left: 28px;
    top: 370px;
    margin: 0;
    padding: 0;
    list-style: none;
    font-family: "Open Sans", sans-serif;
    font-size: 13.5px;
    color: var(--ink);
  }
  .contact-list li {
    display: flex;
    align-items: center;
    height: 21px;
  }
  .contact-list svg {
    width: 10px;
    height: 10px;
    margin-right: 7px;
    fill: var(--brand-blue);
  }
  .social-handle {
    position: absolute;
    left: 28px;
    top: 437px;
    font-family: "Open Sans", sans-serif;
    font-weight: 700;
    font-size: 13.5px;
    color: var(--brand-blue);
  }
</style>
</head>
<body>
<main class="canvas">
  <section class="card card--front" aria-label="Card front">
    <p class="brand-name">ESN</p>
    <p class="tagline">
      <span class="tagline__top">Every Shelf Set</span>
      <span class="tagline__main">NEATLY</span>
    </p>
    <div class="person">
      <p class="person__name">Lorna M. Pelham</p>
      <p class="person__role">Owner</p>
    </div>
    <ul class="contact-list">
      <li>
        <svg viewBox="0 0 10 10" aria-hidden="true"><path d="M2 0.5 L3.6 2.6 L2.7 3.7 C3.3 5 4.9 6.6 6.3 7.3 L7.4 6.4 L9.5 8 L8.4 9.5 C4.5 9.2 0.8 5.5 0.5 1.6 Z"/></svg>
        418-552-7094
      </li>
      <li>
        <svg viewBox="0 0 10 10" aria-hidden="true"><path d="M0.5 2 H9.5 V8.5 H0.5 Z M1 2.4 L5 5.6 L9 2.4" stroke="#f3f3f3" stroke-width="0.8"/></svg>
        info@esnorganized-example.com
      </li>
      <li>
        <svg viewBox="0 0 10 10" aria-hidden="true"><circle cx="5" cy="5" r="4.6"/><path d="M0.6 5 H9.4 M5 0.4 C3 3 3 7 5 9.6 M5 0.4 C7 3 7 7 5 9.6" stroke="#f3f3f3" stroke-width="0.6" fill="none"/></svg>
        www.esnorganized-example.com
      </li>
    </ul>
    <div class="social-handle">everyshelfsetneatly</div>
  </section>

  <section class="card card--back" aria-label="Card back">
    <div class="back-texture" role="img" aria-label="Soft blurred blue textured background"></div>
    <p class="tagline">
      <span class="tagline__top">Every Shelf Set</span>
      <span class="tagline__main">NEATLY</span>
    </p>
  </section>
</main>
</body>
</html>
```